Business Card Design

New business card design

Target Market(s)

Residential & Commercial Property Managers

Industry/Entity Type

Plumbing Services

Contact Information for Business Card

Name - Rowan Keddle, title - Director, Phone Number - 0431 286 517, email - rowan@tbk-plumbing.com.au, Company ABN - 73 215 904 386,

Font styles to use
Sans Serif

Colors
0054AA
0677BA
7BADD7
CADEEF
E8F1F8

```html
<!DOCTYPE html>
<html lang="en">
<head>
<meta charset="utf-8">
<title>TBK Plumbing Services – Business Card</title>
<link rel="stylesheet" href="https://fonts.googleapis.com/css2?family=Montserrat:wght@300;400;500&family=Poppins:wght@700&display=swap">
<style>
  :root {
    --page-bg: #969696;
    --ink: #1e232a;
    --white: #ffffff;
    --water: #0aa9e8;
    --water-soft: #c9ecf9;
    --tagline-grey: #8a8580;
  }
  * { box-sizing: border-box; margin: 0; padding: 0; }
  html, body {
    width: 1200px; height: 1108px; overflow: hidden;
    background: var(--page-bg);
    font-family: "Montserrat", sans-serif;
  }
  .card {
    position: absolute; left: 240px;
    width: 720px; height: 412px;
    border-radius: 28px; overflow: hidden;
  }
  .card--front { top: 120px; background: var(--ink); }
  .card--back { top: 576px; background: var(--white); }

  .wordmark {
    position: absolute;
    font-family: "Montserrat", sans-serif;
    font-weight: 300; line-height: 1;
    letter-spacing: 6px;
    display: flex; align-items: center; gap: 14px;
  }
  .wordmark__dot {
    width: 18px; height: 18px; border-radius: 50%;
    background: var(--water);
  }
  .tagline {
    position: absolute;
    font-family: "Montserrat", sans-serif;
    font-weight: 400; font-size: 15px;
    letter-spacing: 13.5px; white-space: nowrap;
  }

  .card--front .wordmark {
    left: 0; right: 0; top: 132px; justify-content: center;
    font-size: 104px; color: var(--white);
  }
  .card--front .tagline {
    left: 0; right: 0; top: 262px; text-align: center;
    color: var(--white);
  }

  .card--back .wordmark {
    left: 46px; top: 44px; font-size: 86px; color: var(--ink);
  }
  .card--back .tagline {
    left: 68px; top: 156px; font-size: 13px; letter-spacing: 11.5px;
    color: var(--tagline-grey);
  }
  .accent-circle {
    position: absolute; left: 444px; top: 105px;
    width: 270px; height: 270px; border-radius: 50%;
    background: var(--water-soft);
  }
  .contact { position: absolute; left: 45px; top: 236px; color: var(--ink); }
  .contact__name {
    font-family: "Poppins", sans-serif; font-weight: 700;
    font-size: 27px; line-height: 1.1; letter-spacing: -0.3px;
  }
  .contact__role { font-size: 19px; margin-top: 4px; }
  .contact__list { list-style: none; margin-top: 16px; }
  .contact__item {
    display: flex; align-items: center; gap: 14px;
    font-size: 20px; height: 26px;
  }
  .contact__item svg { width: 20px; height: 20px; flex: none; }

  .footer-line {
    position: absolute; left: 0; top: 397px;
    width: 410px; height: 10px;
    background: var(--water);
    clip-path: polygon(0 0, 100% 0, 97% 100%, 0 100%);
  }
  .footer-band {
    position: absolute; left: 0; right: 0; top: 387px; height: 25px;
  }
  .footer-band svg { position: absolute; inset: 0; width: 100%; height: 100%; }
  .footer-band__abn {
    position: absolute; right: 44px; top: 2px;
    color: var(--white); font-size: 19px; white-space: nowrap;
  }
</style>
</head>
<body>
  <section class="card card--front" aria-label="Card front">
    <div class="wordmark">tbk<span class="wordmark__dot"></span></div>
    <p class="tagline">plumbing&nbsp;&nbsp;services</p>
  </section>

  <section class="card card--back" aria-label="Card back">
    <div class="accent-circle"></div>
    <div class="wordmark">tbk<span class="wordmark__dot"></span></div>
    <p class="tagline">plumbing&nbsp;&nbsp;services</p>

    <div class="contact">
      <h1 class="contact__name">Rowan Keddle</h1>
      <p class="contact__role">Director</p>
      <ul class="contact__list">
        <li class="contact__item">
          <svg viewBox="0 0 24 24" aria-hidden="true"><path fill="#0aa9e8" d="M6.6 2.5l3 3.2-1.9 2.6c1.2 2.8 3.4 5 6.2 6.3l2.5-1.9 3.3 3-1.6 3.3c-.4.7-1.2 1-2 .8C9.5 18 5 13.5 3.2 6.9c-.2-.8.1-1.6.8-2z"/></svg>
          0431 286 517
        </li>
        <li class="contact__item">
          <svg viewBox="0 0 24 24" aria-hidden="true"><rect x="1" y="5" width="22" height="15" fill="#0aa9e8"/><path d="M1 5l11 8 11-8" fill="none" stroke="#ffffff" stroke-width="1.8"/></svg>
          rowan@tbk-plumbing.com.au
        </li>
      </ul>
    </div>

    <div class="footer-line"></div>
    <div class="footer-band">
      <svg viewBox="0 0 720 25" preserveAspectRatio="none" aria-hidden="true">
        <polygon points="0,21 403,21 429,0 720,0 720,25 0,25" fill="#1e232a"/>
      </svg>
      <span class="footer-band__abn">ABN - 73 215 904 386</span>
    </div>
  </section>
</body>
</html>
```